Business Card Design

We need a business card designed for our new company. Prefer a black card with white logo & writing.

Contact Information for Business Card

Ted Galloway, address: 7-4812 Fernhollow Road, Abbotsford, BC, V3K 8R2, Office Phone: 604-712-3390, Cell: 604-947-2164, Email: ted@resinworkshub.ca

Colors

Designer to choose only greyscale colors for use in the design.

```html
<!DOCTYPE html>
<html lang="en">
<head>
<meta charset="utf-8">
<title>Resin Works Hub – Business Card</title>
<link rel="stylesheet" href="https://fonts.googleapis.com/css2?family=Figtree:wght@400;700;800&display=swap">
<style>
  :root {
    --backdrop: #262626;
    --card-black: #000000;
    --peak-grey: #404040;
    --paper-white: #ffffff;
    --ink: #111111;
  }
  * { margin: 0; padding: 0; box-sizing: border-box; }
  html, body {
    width: 1200px; height: 900px; overflow: hidden;
    background: var(--backdrop);
    font-family: "Figtree", "Helvetica Neue", Arial, sans-serif;
  }
  .stage { position: relative; width: 1200px; height: 900px; }
  .card {
    position: absolute; left: 341px; width: 518px; height: 296px;
    background: var(--card-black); overflow: hidden;
  }
  .card--front { top: 141px; }
  .card--back { top: 463px; display: flex; align-items: center; justify-content: center; }

  .peak-art { position: absolute; left: 0; top: 130px; width: 518px; height: 166px; display: block; }

  .brand-name {
    color: var(--paper-white); font-weight: 800; text-transform: uppercase;
    letter-spacing: 0.02em; line-height: 1.05; text-align: center;
  }
  .card--front .brand-name {
    position: absolute; left: 27px; top: 36px; width: 130px; font-size: 19px;
  }
  .card--back .brand-name { font-size: 38px; width: 300px; }

  .holder-name {
    position: absolute; left: 0; width: 518px; top: 180px;
    text-align: center; font-size: 18px; font-weight: 800;
    color: var(--ink); letter-spacing: 0.01em; text-transform: uppercase;
  }
  .contact {
    position: absolute; top: 219px; font-size: 13.2px; line-height: 18px;
    color: var(--ink); list-style: none;
  }
  .contact--direct { left: 27px; }
  .contact--place { left: 229px; }
  .contact li { display: flex; align-items: center; gap: 5px; white-space: nowrap; }
  .contact svg { width: 12px; height: 12px; flex: none; }
  .site strong { font-weight: 700; }
  .divider {
    position: absolute; left: 211px; top: 222px; width: 1px; height: 47px;
    background: var(--ink);
  }
</style>
</head>
<body>
<main class="stage">
  <section class="card card--front" aria-label="Card front">
    <svg class="peak-art" role="img" aria-label="Mountain peak illustration in grey and white" viewBox="0 0 518 166" preserveAspectRatio="none">
      <defs>
        <linearGradient id="peakFade" x1="0" y1="0" x2="0" y2="1">
          <stop offset="0" stop-color="#000000"/>
          <stop offset="0.12" stop-color="#404040"/>
          <stop offset="0.3" stop-color="#e6e6e6"/>
          <stop offset="0.42" stop-color="#ffffff"/>
        </linearGradient>
      </defs>
      <rect width="518" height="166" fill="url(#peakFade)"/>
    </svg>

    <p class="brand-name">Resin Works Hub</p>

    <h1 class="holder-name">Ted Galloway</h1>

    <ul class="contact contact--direct">
      <li>
        <svg viewBox="0 0 24 24" aria-hidden="true"><path fill="#111" d="M6.6 10.8a15.2 15.2 0 0 0 6.6 6.6l2.2-2.2a1 1 0 0 1 1-.25 11.4 11.4 0 0 0 3.6.57 1 1 0 0 1 1 1V20a1 1 0 0 1-1 1A17 17 0 0 1 3 4a1 1 0 0 1 1-1h3.5a1 1 0 0 1 1 1c0 1.25.2 2.45.57 3.57a1 1 0 0 1-.25 1z"/></svg>
        604-712-3390
      </li>
      <li>
        <svg viewBox="0 0 24 24" aria-hidden="true"><rect x="6" y="2" width="12" height="20" rx="2" fill="none" stroke="#111" stroke-width="2"/><circle cx="12" cy="18" r="1.2" fill="#111"/></svg>
        604-947-2164
      </li>
      <li>
        <svg viewBox="0 0 24 24" aria-hidden="true"><path fill="#111" d="M2 5h20v14H2z"/><path fill="none" stroke="#fff" stroke-width="1.6" d="M2.5 5.5 12 13l9.5-7.5"/></svg>
        ted@resinworkshub.ca
      </li>
    </ul>

    <span class="divider" aria-hidden="true"></span>

    <ul class="contact contact--place">
      <li>7-4812 Fernhollow Road</li>
      <li>Abbotsford, BC, V3K 8R2</li>
      <li class="site">
        <svg viewBox="0 0 24 24" aria-hidden="true"><g fill="none" stroke="#111" stroke-width="1.8"><circle cx="12" cy="12" r="10"/><ellipse cx="12" cy="12" rx="4.5" ry="10"/><path d="M2 12h20"/></g></svg>
        <span><strong>resinworkshub</strong>.ca</span>
      </li>
    </ul>
  </section>

  <section class="card card--back" aria-label="Card back">
    <p class="brand-name">Resin Works Hub</p>
  </section>
</main>
</body>
</html>
```